Business Cards - Brightpath Horizon

need to design unique business card for my mortgage business. I need to design credit card style business card for my business or any unique idea that you might have

Target Market(s)

Home Loan customers

Industry/Entity Type

Mortgage Brokerage

Contact Information for Business Card

please design credit card style or very unique style business card

Colors

Designer to choose colors to be used in the design.

Requirements
Must have
• Name
• position
• Phone number
• fax number
• email address
• website address
• social media address
• All above fields will be provided once design in finalised

```html
<!DOCTYPE html>
<html lang="en">
<head>
<meta charset="UTF-8">
<title>Brightpath Horizon – Business Card</title>
<link href="https://fonts.googleapis.com/css2?family=Lato:wght@400;700&family=Lora:wght@600&display=swap" rel="stylesheet">
<style>
  :root {
    --brand-blue: #0433c4;
    --brand-blue-light: #2f5be0;
    --brand-orange: #f7941d;
    --card-white: #ffffff;
    --ink: #1a1a1a;
    --backdrop: #e9e9ec;
  }
  html, body {
    margin: 0;
    padding: 0;
    width: 1200px;
    height: 900px;
    overflow: hidden;
    background: var(--backdrop);
  }
  .business-card {
    position: absolute;
    left: 111px;
    top: 148px;
    width: 978px;
    height: 605px;
    background: var(--card-white);
    box-shadow: 0 10px 30px rgba(0,0,0,0.18);
    overflow: hidden;
  }
  .roofline-art {
    position: absolute;
    left: 0;
    top: 0;
    width: 100%;
    height: 246px;
    background: linear-gradient(100deg, var(--brand-blue) 0%, var(--brand-blue) 55%, var(--brand-blue-light) 100%);
  }
  .social-handle {
    position: absolute;
    left: 54px;
    top: 80px;
    margin: 0;
    font-family: "Lato", sans-serif;
    font-weight: 700;
    font-size: 24px;
    color: var(--card-white);
  }
  .footer-band {
    position: absolute;
    left: 0;
    bottom: 0;
    width: 100%;
    height: 35px;
    background: var(--brand-blue);
  }
  .holder-name {
    position: absolute;
    left: 60px;
    top: 300px;
    margin: 0;
    font-family: "Lora", serif;
    font-weight: 600;
    font-size: 31px;
    letter-spacing: 1px;
    color: var(--brand-blue);
    text-transform: uppercase;
  }
  .holder-role {
    position: absolute;
    left: 61px;
    top: 342px;
    margin: 0;
    font-family: "Lato", sans-serif;
    font-size: 24px;
    color: var(--ink);
  }
  .contact-list {
    position: absolute;
    left: 60px;
    top: 408px;
    margin: 0;
    padding: 0;
    list-style: none;
    font-family: "Lato", sans-serif;
    font-size: 25px;
    color: var(--ink);
  }
  .contact-list li {
    display: flex;
    align-items: center;
    height: 35px;
  }
  .contact-list svg {
    width: 20px;
    height: 20px;
    margin-right: 16px;
    fill: var(--brand-blue);
  }
  .brand-mark {
    position: absolute;
    left: 540px;
    top: 398px;
    display: flex;
    align-items: center;
    gap: 14px;
  }
  .brand-mark .brand-square {
    width: 22px;
    height: 22px;
    background: var(--brand-orange);
    flex: none;
  }
  .brand-mark .brand-name {
    font-family: "Lora", serif;
    font-weight: 600;
    font-size: 38px;
    color: var(--brand-blue);
    white-space: nowrap;
  }
</style>
</head>
<body>
  <div class="business-card">
    <div class="roofline-art" role="img" aria-label="Roofline illustration of two houses with windows and an orange trim"></div>

    <p class="social-handle">@brightpathhorizon</p>

    <h1 class="holder-name">Marcus Ellery</h1>
    <p class="holder-role">Managing Director</p>

    <ul class="contact-list">
      <li>
        <svg viewBox="0 0 20 20"><path d="M2 7c0-3 3-4 8-4s8 1 8 4l-3 1-1-2H6L5 8zM5 10h10l2 7H3z"/></svg>
        (044)555018273
      </li>
      <li>
        <svg viewBox="0 0 20 20"><path d="M5 1h8l2 2v5H5zM2 8h16v10H2zM5 11h10v2H5zM5 14h6v2H5z"/></svg>
        (044)555018273
      </li>
      <li>
        <svg viewBox="0 0 20 20"><path d="M1 4h18v1L10 11 1 5zM1 7l9 6 9-6v9H1z"/></svg>
        hello@brightpathhorizon.com
      </li>
      <li>
        <svg viewBox="0 0 20 20"><circle cx="10" cy="10" r="9"/><path d="M6 5c2 1 3 3 2 5s-2 3 0 5M12 3c-1 2 2 3 3 5s-2 4-1 6" stroke="#fff" stroke-width="1.5" fill="none"/></svg>
        www.brightpathhorizon.com
      </li>
    </ul>

    <div class="brand-mark">
      <span class="brand-square"></span>
      <span class="brand-name">Brightpath Horizon</span>
    </div>

    <div class="footer-band"></div>
  </div>
</body>
</html>
```